In need of an AWESOME website for our Water Re-filling Store

The project is to design a website for our retail store front with the website www.quellbrookfillhouse.com. Currently if you go to that site it redirects you to our other site www.quellbrookbottleworks.com which is just our water bottle website. So, I need a new website created for www.quellbrookfillhouse.com (retail storefront)
Use our Squarespace to create a site with pages to help educate, tell about us, link to our water bottle brand site that is already created with Squarespace, and show the family and community aspects that we believe in. Our current water bottle website is www.quellbrookbottleworks.com for reference
We also sell hydration products, especially PRZQ products and have access to digital media through our PRZQ dealer site. we sell bottles, dispensers and other supplies for water refilling customers. We sell Ice as well.

Target Market(s)

Local residents looking to fill up their 1-5 gallon water jugs

Industry/Entity Type

Alkaline and Purified Water Retail Re-filling Store

Coding

Coded - Design and coding required

Font styles to use
Serif
Sans Serif

Colors
0054AA
0677BA
7BADD7
CADEEF
E8F1F8

Requirements
Must have
• pictures of our family in the about us section and pictures of our store inside and out.

```html
<!DOCTYPE html>
<html lang="en">
<head>
<meta charset="utf-8">
<title>Quellbrook Fill House</title>
<link href="https://fonts.googleapis.com/css2?family=Libre+Baskerville:wght@400;700&family=Poppins:wght@400;500;600&display=swap" rel="stylesheet">
<style>
:root{
  --blue:#3a55a8;
  --blue-deep:#2f4793;
  --ink:#1f1f24;
  --text:#3a3a44;
  --muted:#5b5b66;
  --mist:#e8edf7;
  --navy:#1e2030;
  --white:#ffffff;
  --line:#dfe3ec;
  --serif:'Libre Baskerville', Georgia, serif;
  --sans:'Poppins', Arial, sans-serif;
}
*{box-sizing:border-box;margin:0;padding:0}
html,body{width:1200px;height:3143px;overflow:hidden}
body{position:relative;background:var(--white);font-family:var(--sans);color:var(--text)}
.abs{position:absolute}

/* hero */
.hero{left:0;top:0;width:1200px;height:681px;
  background:linear-gradient(180deg,#5a6b7a 0%,#7b6a5e 18%,#3d5a72 30%,#2e4a63 60%,#2a3f55 100%)}
.hero-shade{left:0;top:0;width:1200px;height:681px;background:linear-gradient(90deg,rgba(15,25,40,.55) 0%,rgba(15,25,40,.15) 55%,rgba(15,25,40,.25) 100%)}
.brand{left:130px;top:14px;width:80px;text-align:center;color:var(--white);font-family:var(--serif);font-weight:700;font-size:10px;line-height:12px;letter-spacing:.5px}
.brand-phone{display:block;font-size:7px;line-height:10px}
.nav{top:28px;display:flex;gap:28px;font-size:10px;color:var(--white);letter-spacing:.3px;white-space:nowrap}
.nav-top{right:260px}
.call-btn{left:961px;top:20px;width:107px;height:31px;border-radius:16px;background:var(--blue);color:var(--white);font-size:10.5px;font-weight:600;display:flex;align-items:center;justify-content:center;white-space:nowrap}
.hero-title{left:132px;top:240px;font-family:var(--serif);font-weight:700;font-size:40px;line-height:47px;color:var(--white);letter-spacing:.5px}
.hero-sub{left:132px;top:400px;width:350px;font-size:10.5px;line-height:16px;color:var(--white)}
.btn{display:flex;align-items:center;justify-content:center;border-radius:17px;font-family:var(--serif);font-weight:700;font-size:9.5px;letter-spacing:.3px;white-space:nowrap}
.btn-light{background:var(--white);color:var(--blue)}
.btn-ghost{border:1px solid var(--white);color:var(--white)}
.btn-blue{background:var(--blue);color:var(--white)}
.video-label{left:918px;top:328px;font-family:var(--serif);font-weight:700;font-size:16px;line-height:21px;color:var(--white)}
.play{left:881px;top:390px;width:99px;height:99px;border-radius:50%;background:var(--white)}
.drop-deco{left:890px;top:50px;width:310px;height:440px;border-radius:50% 50% 50% 50%/40% 40% 60% 60%;background:rgba(255,255,255,.06)}

/* headings */
.h2{font-family:var(--serif);font-weight:700;color:var(--blue);text-align:center;letter-spacing:.5px}

/* offer cards */
.card{top:844px;width:229px;height:294px;background:var(--white);border-radius:14px;box-shadow:0 4px 18px rgba(30,40,80,.09);text-align:center}
.card-photo{margin:6px;height:207px;border-radius:12px}
.card-title{margin-top:26px;font-family:var(--serif);font-size:14px;color:var(--ink)}
.card-sub{margin-top:6px;font-size:9.5px;color:var(--text)}

/* purpose */
.circle-photo{border-radius:50%}
.purpose-title{left:579px;top:1300px;font-family:var(--serif);font-weight:700;font-size:23px;line-height:28px;color:var(--blue)}
.purpose-text{left:579px;top:1370px;width:456px;font-size:9.8px;line-height:15.6px;color:var(--text)}

/* local spot */
.wave{left:0;top:1690px;width:1200px;height:520px}
.feature{top:1945px;width:240px;text-align:center}
.feature-label{margin-top:20px;font-family:var(--serif);font-size:14.5px;line-height:19px;color:var(--ink)}
.vline{top:1975px;width:1px;height:135px;background:var(--line)}

/* store rows */
.row-line{left:132px;width:935px;height:1px;background:var(--line)}
.row-title{left:261px;font-family:var(--serif);font-weight:700;font-size:15px;color:var(--blue)}
.row-text{left:613px;width:440px;font-size:9.8px;line-height:15.5px;color:var(--text)}

/* cta */
.footer-bg{left:0;top:2738px;width:1200px;height:363px;background:var(--navy)}
.cta{left:132px;top:2612px;width:936px;height:266px;border-radius:18px;background:var(--blue)}
.cta-title{left:217px;top:2677px;font-family:var(--serif);font-weight:700;font-size:22px;color:var(--white);letter-spacing:.5px}
.cta-text{left:216px;top:2713px;width:520px;font-size:9.8px;line-height:15.5px;color:var(--white)}
.ring{left:793px;top:2660px;width:218px;height:218px;border-radius:50%;border:12px solid var(--white);border-bottom-color:transparent;border-right-color:transparent;transform:rotate(-20deg)}
.cta-photo{left:755px;top:2561px;width:250px;height:317px;border-radius:120px 120px 0 0;background:linear-gradient(180deg,#e6d3bf 0%,#f1efec 45%,#dfe3ea 75%,#3e5d8c 100%)}

/* footer */
.foot-brand{left:130px;top:2925px;width:135px;text-align:center;color:var(--white);font-family:var(--serif);font-weight:700;font-size:18px;line-height:21px;letter-spacing:.5px}
.foot-brand .brand-phone{font-size:11px;line-height:16px}
.contact{top:2964px;display:flex;align-items:center;gap:12px;color:var(--white);font-size:10px;font-weight:600;white-space:nowrap}
.contact-dot{width:28px;height:28px;border-radius:50%;background:#34374a;display:flex;align-items:center;justify-content:center}
.nav-foot{right:194px;top:3012px;gap:30px}
.chat{left:1126px;top:3032px;width:30px;height:28px}
.legal{left:0;top:3101px;width:1200px;height:42px;background:var(--white)}
.copy{left:128px;top:3115px;font-size:9px;color:var(--ink)}
.social{top:3115px;width:11px;height:11px;border:1.5px solid var(--ink);border-radius:3px}
</style>
</head>
<body>

<!-- hero -->
<div class="abs hero" role="img" aria-label="Family by a lake at sunset, father lifting a young boy while the mother smiles"></div>
<div class="abs hero-shade"></div>
<div class="abs drop-deco"></div>
<div class="abs brand">QUELLBROOK<br>FILL HOUSE<span class="brand-phone">555-014-2290</span></div>
<nav class="abs nav nav-top"><span>HOME</span><span>OUR WATER</span><span>WHY ALUMINUM</span><span>FILL HOUSE WELLNESS BLOG</span><span>CONTACT</span></nav>
<div class="abs call-btn">555-014-2290</div>
<h1 class="abs hero-title">PURE HYDRATION<br>FOR YOUR<br>EVERYDAY LIFE</h1>
<p class="abs hero-sub">Clean, alkaline and purified water for your home and family. Refill, refresh, and stay hydrated with us.</p>
<div class="abs btn btn-light" style="left:132px;top:455px;width:123px;height:33px">VISIT OUR STORE</div>
<div class="abs btn btn-ghost" style="left:262px;top:455px;width:123px;height:33px">GET DIRECTIONS</div>
<div class="abs video-label">CLICK TO<br>PLAY VIDEO</div>
<svg class="abs" style="left:995px;top:355px" width="80" height="95" viewBox="0 0 80 95" fill="none" stroke="#fff" stroke-width="2.5" stroke-linecap="round">
  <path d="M40 4c30 2 40 30 20 50-14 14-30 4-22-8 8-12 24 0 14 14-8 10-22 18-38 18"/>
  <path d="M14 72l-8 6 9 5"/>
</svg>
<div class="abs play"></div>
<svg class="abs" style="left:920px;top:428px" width="22" height="24" viewBox="0 0 22 24"><path d="M2 2l18 10L2 22z" fill="var(--blue)"/></svg>

<!-- what we offer -->
<h2 class="abs h2" style="left:0;top:780px;width:1200px;font-size:29px">WHAT WE OFFER</h2>
<div class="abs card" style="left:122px">
  <div class="card-photo" role="img" aria-label="Man in a blue shirt carrying two large water jugs" style="background:linear-gradient(160deg,#9fb88a 0%,#2f64c4 55%,#c9d6e6 100%)"></div>
  <div class="card-title">WATER REFILLS</div><div class="card-sub">Affordable 1–5 gallon refill solutions</div>
</div>
<div class="abs card" style="left:364px">
  <div class="card-photo" role="img" aria-label="Woman holding a skincare hydration bottle" style="background:linear-gradient(160deg,#f2f2f2 0%,#e6cdbd 50%,#f4f4f4 100%)"></div>
  <div class="card-title">HYDRATION PRODUCTS</div><div class="card-sub">Bottles, electrolytes, dispensers &amp; more</div>
</div>
<div class="abs card" style="left:606px">
  <div class="card-photo" role="img" aria-label="Water bottles resting on ice cubes" style="background:linear-gradient(160deg,#c8d3dc 0%,#3aa7de 45%,#2a2f36 100%)"></div>
  <div class="card-title">ICE SUPPLY</div><div class="card-sub">Fresh ice available daily</div>
</div>
<div class="abs card" style="left:849px">
  <div class="card-photo" role="img" aria-label="Family of several generations greeting each other" style="background:linear-gradient(160deg,#dde4ea 0%,#8a9bb0 50%,#5a6e8c 100%)"></div>
  <div class="card-title">FAMILY-OWNED</div><div class="card-sub">Serving our community with care</div>
</div>

<!-- purpose -->
<div class="abs circle-photo" role="img" aria-label="Man drinking from a water bottle on a green hillside" style="left:174px;top:1269px;width:310px;height:310px;background:linear-gradient(160deg,#8a9a6b 0%,#b7a592 45%,#2b2a2c 100%)"></div>
<div class="abs circle-photo" role="img" aria-label="Water poured from a bottle into an aluminum cup outdoors" style="left:353px;top:1463px;width:170px;height:170px;border:4px solid #fff;background:linear-gradient(160deg,#cfd8dc 0%,#6a7f60 50%,#c7b8b0 100%)"></div>
<h2 class="abs purpose-title">A PURPOSE-DRIVEN<br>BOTTLED WATER BRAND</h2>
<p class="abs purpose-text">At Quellbrook Bottleworks, hydration goes far beyond simply quenching thirst; it represents a deep commitment to enhancing both personal health and environmental sustainability. Drawing inspiration from the resilient and vibrant spirit of Tucson, AZ, the brand delivers a premium alkaline water experience thoughtfully designed to meet the needs of today's health-conscious and eco-aware consumers. Their cold-filled, ultra-purified alkaline water is carefully formulated to help neutralize body acidity, support optimal hydration, assist in natural detoxification processes, and promote sustained energy levels throughout the day. Packaged in sturdy, reusable aluminum bottles, it perfectly combines sleek, modern design with a strong focus on sustainability. Each bottle is a symbol of their unwavering dedication to providing quality hydration that benefits not only the body but also respects and protects the planet, encouraging a meaningful and lasting shift toward responsible consumption—one thoughtfully crafted bottle at a time.</p>
<div class="abs btn btn-blue" style="left:579px;top:1580px;width:123px;height:32px">READ MORE</div>

<!-- local spot -->
<svg class="abs wave" viewBox="0 0 1200 520" preserveAspectRatio="none">
  <defs><linearGradient id="mistFade" x1="0" y1="0" x2="0" y2="1"><stop offset="0" stop-color="#e8edf7"/><stop offset="1" stop-color="#ffffff"/></linearGradient></defs>
  <path d="M0 80C180 120 300 110 520 70 760 20 900-10 1050 20 1120 35 1170 55 1200 72V520H0z" fill="url(#mistFade)"/>
</svg>
<h2 class="abs h2" style="left:0;top:1880px;width:1200px;font-size:23px">YOUR LOCAL HYDRATION SPOT</h2>

<div class="abs feature" style="left:114px">
  <svg width="84" height="76" viewBox="0 0 84 76" fill="none" stroke="var(--blue)" stroke-width="2.5"><circle cx="42" cy="18" r="14"/><path d="M42 9c-5 7-6 10-6 12a6 6 0 0012 0c0-2-1-5-6-12z" fill="var(--blue)"/><path d="M6 36h72M14 36v6h56v-6"/><path d="M18 46h10l-2 26h-6zM37 46h10l-2 26h-6zM56 46h10l-2 26h-6z" fill="var(--blue)"/></svg>
  <div class="feature-label">HIGH-QUALITY<br>ALKALINE<br>&amp; PURIFIED WATER</div>
</div>
<div class="abs vline" style="left:363px"></div>
<div class="abs feature" style="left:365px">
  <svg width="84" height="76" viewBox="0 0 84 76" fill="none" stroke="var(--blue)" stroke-width="2.5"><path d="M48 6h12v8h-12zM42 18c0-4 4-4 4-4h16s4 0 4 4l4 8v22H38V26z" fill="var(--blue)"/><path d="M4 40h16c6 0 10 6 18 6h14M20 40v26h-16M20 62h16l28-8c4-1 6 4 2 6l-22 12H20"/></svg>
  <div class="feature-label">AFFORDABLE<br>REFILL PRICING</div>
</div>
<div class="abs vline" style="left:610px"></div>
<div class="abs feature" style="left:602px">
  <svg width="84" height="76" viewBox="0 0 84 76" fill="none" stroke="var(--blue)" stroke-width="2.5"><path d="M42 20c-8-6-14-10-14-15a6 6 0 0114-2 6 6 0 0114 2c0 5-6 9-14 15z"/><circle cx="32" cy="34" r="4" fill="var(--blue)"/><circle cx="52" cy="34" r="4" fill="var(--blue)"/><circle cx="42" cy="32" r="4" fill="var(--blue)"/><path d="M26 52c0-8 32-8 32 0z" fill="var(--blue)"/><path d="M6 30v24l18 16M78 30v24L60 70M14 40l14 16M70 40L56 56"/></svg>
  <div class="feature-label">FRIENDLY,<br>FAMILY-DRIVEN<br>SERVICE</div>
</div>
<div class="abs vline" style="left:837px"></div>
<div class="abs feature" style="left:840px">
  <svg width="84" height="76" viewBox="0 0 84 76" fill="none" stroke="var(--blue)" stroke-width="2.5"><path d="M18 4h48v8H18z" fill="var(--blue)"/><path d="M22 12l4 60h32l4-60"/><path d="M36 34l6-8 6 8M50 42l-4 8h-10M32 48l-4-6 4-6"/><circle cx="60" cy="64" r="9" fill="var(--blue)"/></svg>
  <div class="feature-label">CLEAN AND SAFE<br>ENVIRONMENT</div>
</div>

<!-- visit our store -->
<h2 class="abs h2" style="left:0;top:2186px;width:1196px;font-size:23px">VISIT OUR STORE</h2>
<svg class="abs" style="left:180px;top:2254px" width="58" height="58" viewBox="0 0 58 58" fill="none" stroke="var(--blue)" stroke-width="2.5"><path d="M4 4h50v12H4z" fill="var(--blue)"/><path d="M2 16h54v8H2z" fill="var(--blue)"/><path d="M8 24v32h42V24M20 40h18v16H20z"/><path d="M29 46c-3-4-6-4-6 0 0 2 3 4 6 6 3-2 6-4 6-6 0-4-3-4-6 0z"/></svg>
<div class="abs row-title" style="top:2275px">STORE EXTERIOR</div>
<p class="abs row-text" style="top:2268px">Our store exterior is designed to be clean, visible, and welcoming, making it easy for customers to locate and access our facility.</p>
<div class="abs row-line" style="top:2328px"></div>

<svg class="abs" style="left:180px;top:2352px" width="58" height="58" viewBox="0 0 58 58" fill="none" stroke="var(--blue)" stroke-width="2.5"><path d="M2 4h54v8H2z" fill="var(--blue)"/><path d="M6 12v44h46V12M6 40h46M22 40v16M36 40v16M14 26h14v14H14z"/><path d="M36 20h10v16H36z"/></svg>
<div class="abs row-title" style="top:2372px">STORE INTERIOR</div>
<p class="abs row-text" style="top:2365px">Our store interior is designed to be clean, organized, and easy to navigate, ensuring a smooth and efficient experience for every customer.</p>
<div class="abs row-line" style="top:2434px"></div>

<svg class="abs" style="left:180px;top:2455px" width="58" height="58" viewBox="0 0 58 58" fill="none" stroke="var(--blue)" stroke-width="2.5"><path d="M29 2l3 6 6 1-4 4 1 6-6-3-6 3 1-6-4-4 6-1z" fill="var(--blue)"/><path d="M9 12l2 4 4 1-3 3 1 4-4-2-4 2 1-4-3-3 4-1zM49 12l2 4 4 1-3 3 1 4-4-2-4 2 1-4-3-3 4-1z"/><circle cx="29" cy="30" r="6"/><circle cx="13" cy="38" r="5"/><circle cx="45" cy="38" r="5"/><path d="M17 56c0-10 24-10 24 0z" fill="var(--blue)"/><path d="M3 56c0-8 16-10 18-4M55 56c0-8-16-10-18-4"/></svg>
<div class="abs row-title" style="top:2477px">CUSTOMER EXPERIENCE</div>
<p class="abs row-text" style="top:2470px">Our customer experience is centered around convenience, quality, and care. We aim to make every visit smooth and hassle-free, whether customers are refilling water,</p>

<!-- cta -->
<div class="abs footer-bg"></div>
<div class="abs cta"></div>
<div class="abs cta-photo" role="img" aria-label="Smiling woman in a white shirt pouring water into a glass"></div>
<div class="abs ring"></div>
<h2 class="abs cta-title">REFILL. REFRESH. REPEAT.</h2>
<p class="abs cta-text">Refill. Refresh. Repeat. represents our simple and consistent approach to hydration. We make it easy for customers to refill their water containers with clean, high-quality water, refresh their bodies with better hydration, and return whenever they need a reliable and convenient solution for their daily water needs.</p>
<div class="abs btn btn-light" style="left:213px;top:2782px;width:123px;height:31px">VISIT US TODAY</div>

<!-- footer -->
<div class="abs foot-brand">QUELLBROOK<br>FILL HOUSE<span class="brand-phone">555-014-2290</span></div>
<div class="abs contact" style="left:740px">
  <span class="contact-dot"><svg width="11" height="11" viewBox="0 0 12 12"><path d="M2 1l3 0 1 3-2 1c1 2 2 3 3 3l1-2 3 1v3c-6 0-10-4-10-10z" fill="#fff"/></svg></span>555-014-2290
</div>
<div class="abs contact" style="left:872px">
  <span class="contact-dot"><svg width="11" height="9" viewBox="0 0 12 9"><path d="M0 0h12v9H0z" fill="#fff"/><path d="M0 0l6 5 6-5" fill="none" stroke="#34374a" stroke-width="1.2"/></svg></span>HELLO@QUELLBROOKMAIL.COM
</div>
<nav class="abs nav nav-foot"><span>HOME</span><span>OUR WATER</span><span>WHY ALUMINUM</span><span>FILL HOUSE WELLNESS BLOG</span><span>CONTACT</span></nav>
<svg class="abs chat" viewBox="0 0 30 28"><path d="M15 2C7 2 1 7 1 13c0 3 2 6 5 8l-2 6 7-4c1 0 3 1 4 1 8 0 14-5 14-11S23 2 15 2z" fill="#fff"/><circle cx="9" cy="13" r="2" fill="var(--navy)"/><circle cx="15" cy="13" r="2" fill="var(--navy)"/><circle cx="21" cy="13" r="2" fill="var(--navy)"/></svg>
<div class="abs legal"></div>
<div class="abs copy">© 2026 QUELLBROOK FILL HOUSE. ALL RIGHTS RESERVED</div>
<div class="abs social" style="left:1021px;border-radius:50%"></div>
<div class="abs social" style="left:1055px"></div>

</body>
</html>
```